Flyer for an pediatric sleep consultancy - to distribute to play and childcare centers etc.

I need a flyer that will attract the attention of parents with children between the age of babies to toddlers, who may be experiencing sleep issues. The flyer will be placed at places such as community centers, doctors room, play centers, kindergardens, etc.

My company is called "The Quiet Meadow Nest" and provides a sleep consultancy service. My service essentially provides a customized plan for parents to follow and general advice and guidance. It is not medical advice.

I like to the flyer to have an overall tone that is soft and peaceful with a clean and beautiful design, however can catch the attention of parents who may be struggling with their child's sleep issues and are sleep deprived. I would like photos with minimal text. The colour I use is a brownish rose. I will attach some of my designs to give you an idea. You can have a look at my homepage as well to get an idea about my esthetic direction and the colour. Although the colour of my page is a bit too brownish....

I will provide the text to appear in the flyer once I have a better idea of the layout that I prefer for the flyer. The text however wont be extensive, just some catchy points.

I want to direct people to my website which is www.quietmeadownest-example.com
I offer a first FREE evaluation call, to the parents, to get to know each other better, learn about their child's particular sleep problems and see if we are a good fit and can work together. I would like to have this information somehow on the flyer, so that the parents will contact me.
I also have a facebook page, which is: The Quiet Meadow Nest

I have a logo that I would like to appear on the flyer. I will attach the file once the uploader on pixel guild is fixed.

When I print the flyer - I like to print A5 SIZE ... please make sure the formatting is OK for this size.

Here are some text ideas. of course all of it would be too much, I guess. On the front of the flyer I would like to have some catchy phrase or something similar to get people interested and to want to know more. On the back there could be a bit more text and information. But I'm open too suggestions....
I'm not too sure about the wording yet. But here are some text that I might be use:

Is sleep an issue in your home?

Is your baby having trouble sleeping? ... are you?!
I can help!

Sleep, baby, sleep….

Teaching children how to sleep

The Quiet Meadow Nest is a pediatric sleep consultancy that specializes in helping parents with children who struggle to develop good and healthy sleep habits.
Disruptive sleep patterns or not enough sleep can affect the physical, mental and emotional development of your child.

Of course nobody plans to have a sleep problem, but habits can become easily ingrained and spiral quickly out of control and you can find yourself sleep deprived, desperate and not too sure what to do. You see all the other sleeping babies and wish there was someone who understood what you were going through?! Well, there is!

Contact me for a free 15 minute consultation.

This 15 minute „mini“ consultation is a chance to discuss your unique sleep challenges and sleep goals with me. I will provide you with an overview of how I will work with your family to achieve your wildest sleep dreams (goals).
Furthermore do I understand and believe that every child and their family is unique and there is no one size fits all!
I would love to have a chat with you and talk about how I can help make things easier for you and your family!

Do I need a sleep consultant for my child?
The answer is yes if:
- if your child will only fall asleep when nursing or bottle feeding
- if your child needs a dummy or other external aid, like being rocked, patted or taken for a care ride to fall asleep
- if your good night routine is a challenging and exhausting procedure instead of a relaxed and enjoyable moment for the whole family
- if sleep is a constant battle in your home which leaves you feeling frustrated and exhausted
- if your own lack of sleep is taking a toll on you and the whole family

What can I do for you?

I will:

- Guide you to set an age appropriate foundation for good sleep
- Create an individual sleep plan tailored especially to your child’s sleep needs and circumstances
- Help you to teach your childto go to sleep and get back to sleep independently during the night
- show you how to teach your child to take healthful, restorative naps
-Learn

Contact:

Marta Lindqvist
info@quietmeadownest-example.com
www.quietmeadownest-example.com
+34 612 384 705

Consultations in English, German or Spanish via Phone/Skype or home consultation
Updates

Project Deadline Extended
Reason: I have to go on a business trip and won't be able to choose a design until the deadline. During the trip I won't have time to give feedback and ask for changes. thank you

Target Market(s)

parents, sleep deprived mothers, young families, child care provider,

Industry/Entity Type

Baby Care

Contact Information for Business Card

Marta Lindqvist
pediatric sleep consultant
+34 612 384 705

```html
<!DOCTYPE html>
<html lang="en">
<head>
<meta charset="utf-8">
<title>The Quiet Meadow Nest – Flyer</title>
<link href="https://fonts.googleapis.com/css2?family=Signika:wght@300;400;600&family=Lato:wght@400;700&display=swap" rel="stylesheet">
<style>
  :root{
    --bg:#efe9e4;
    --paper:#ffffff;
    --peach:#f5c7b5;
    --peach-text:#f0b49c;
    --teal:#a9c3b8;
    --teal-text:#9dbab0;
    --ink:#4a4644;
    --ink-soft:#222;
    --muted:#9a9a9a;
  }
  *{box-sizing:border-box;margin:0;padding:0}
  html,body{width:1200px;height:1200px;overflow:hidden;background:var(--bg)}
  .canvas{position:relative;width:1200px;height:1200px}
  .page{position:absolute;top:217px;width:540px;height:766px;background:var(--paper);overflow:hidden;
    box-shadow:0 2px 8px rgba(0,0,0,.12);font-family:"Lato",sans-serif;color:var(--ink-soft)}
  .page--front{left:40px}
  .page--back{left:620px}
  .abs{position:absolute}
  .photo{position:absolute}
  .wave{position:absolute;left:0;width:540px}

  /* front */
  .hero-photo{left:0;top:0;width:540px;height:340px;background:linear-gradient(135deg,#e9d6cb 0%,#f3ece7 45%,#d9c3b6 100%)}
  .brand{left:18px;top:362px;width:250px;text-align:center;font-family:"Signika",sans-serif;font-weight:300;font-size:18px;color:var(--muted)}
  .brand__dot{display:block;width:40px;height:40px;border:1.5px solid var(--peach-text);border-radius:50%;margin:0 auto 8px}
  .headline{right:20px;text-align:right;font-family:"Signika",sans-serif;font-weight:600;white-space:nowrap}
  .headline--one{top:280px;font-size:34px;line-height:39px}
  .headline--two{top:368px;font-size:30px;line-height:34px}
  .peach{color:var(--peach-text)}
  .teal{color:var(--teal-text)}
  .help-band{left:0;top:480px;width:540px;height:192px;background:var(--peach)}
  .help{left:18px;font-family:"Signika",sans-serif;font-weight:400;line-height:1;white-space:nowrap}
  .help--a{top:495px;font-size:31px;color:var(--ink)}
  .help--b{top:537px;font-size:29px;color:#fff}
  .help--c{top:578px;font-size:34px;color:var(--ink);font-weight:600;transform:scaleX(.86);transform-origin:left}
  .help--d{top:618px;font-size:40px;color:#fff;font-weight:600;transform:scaleX(.82);transform-origin:left}
  .consultant-photo{left:332px;top:445px;width:190px;height:321px;background:linear-gradient(180deg,#f7f3ef 0%,#e8d7c9 55%,#3d3a3a 100%)}
  .front-footer{left:0;top:697px;width:540px;height:69px}
  .contact-front{color:#fff;font-size:10.5px;line-height:18px;white-space:nowrap}
  .contact-front svg{vertical-align:-2px;margin-right:5px}

  /* back */
  .top-photo{left:0;top:0;width:540px;height:135px;background:linear-gradient(90deg,#eef0f1 0%,#f4f4f4 55%,#e6d3c7 78%,#f2f2f2 100%)}
  .body-copy{left:17px;width:506px;font-size:10.4px;line-height:13.2px;color:#222}
  .body-copy p+p{margin-top:6px}
  .intro{top:148px}
  .offer-band{left:0;top:256px;width:540px;height:137px;background:var(--peach)}
  .offer-title{left:18px;top:274px;font-family:"Signika",sans-serif;font-weight:600;font-size:22.5px;line-height:27px;color:var(--ink)}
  .offer-side{left:265px;top:265px;width:258px;font-size:10.4px;line-height:13.2px;text-align:justify}
  .offer-more{left:18px;top:343px;width:505px;font-size:10.4px;line-height:13.2px}
  .section-title{left:18px;font-weight:700;font-size:12.5px;line-height:16px}
  .checklist{left:18px;width:505px;list-style:none;font-size:10px;line-height:12.8px}
  .checklist li{position:relative;padding-left:16px}
  .checklist li svg{position:absolute;left:0;top:2px}
  .back-photo{left:270px;top:650px;width:270px;height:116px;background:linear-gradient(160deg,#f3ece6 0%,#e4cbb8 50%,#f1efed 100%)}
  .contact-back{left:20px;top:695px;font-size:11px;line-height:17px;color:#222;letter-spacing:.2px}
  .contact-back svg{vertical-align:-2px;margin-right:5px}
</style>
</head>
<body>
<main class="canvas">

  <!-- FRONT -->
  <section class="page page--front">
    <div class="photo hero-photo" role="img" aria-label="Photo of a mother resting beside her sleeping baby on white bedding"></div>
    <svg class="wave" style="top:200px" height="150" viewBox="0 0 540 150" aria-hidden="true">
      <path d="M0 110 C180 50 360 35 540 8 L540 150 L0 150 Z" fill="var(--teal)"/>
      <path d="M0 132 C180 72 360 52 540 22 L540 150 L0 150 Z" fill="var(--peach)"/>
      <path d="M0 140 C180 80 360 58 540 28 L540 150 L0 150 Z" fill="#fff"/>
    </svg>

    <div class="abs brand"><span class="brand__dot"></span>The Quiet Meadow Nest</div>

    <h1 class="abs headline headline--one"><span class="peach">Is sleep an issue</span><br><span class="teal">in your home?</span></h1>
    <h2 class="abs headline headline--two"><span class="peach">Is your baby having</span><br><span class="teal">trouble sleeping?</span></h2>

    <div class="abs help-band"></div>
    <p class="abs help help--a">I can help!</p>
    <p class="abs help help--b">Sleep, baby, sleep</p>
    <p class="abs help help--c">Teaching children</p>
    <p class="abs help help--d">HOW TO SLEEP</p>

    <svg class="front-footer abs" viewBox="0 0 540 69" aria-hidden="true">
      <path d="M0 14 C150 -4 330 0 540 12 L540 69 L0 69 Z" fill="var(--teal)"/>
      <path d="M0 12 C150 -6 330 -2 540 8" fill="none" stroke="var(--peach)" stroke-width="2"/>
    </svg>
    <div class="photo consultant-photo" role="img" aria-label="Photo of the sleep consultant holding a smiling toddler"></div>

    <div class="abs contact-front" style="left:18px;top:718px">
      <div><svg width="10" height="10" viewBox="0 0 10 10"><circle cx="5" cy="3" r="2.3" fill="#fff"/><path d="M1 10 C1 6 9 6 9 10Z" fill="#fff"/></svg>MARTA LINDQVIST</div>
      <div><svg width="10" height="10" viewBox="0 0 10 10"><path d="M2 1 L4 1 L5 3.5 L3.7 4.5 C4.3 5.8 5 6.5 6.3 7.2 L7.4 6 L9.6 7 L9.4 9 C5 9.5 0.6 5 1.2 1.3Z" fill="#fff"/></svg>+34 612 384 705</div>
    </div>
    <div class="abs contact-front" style="left:126px;top:718px">
      <div><svg width="11" height="9" viewBox="0 0 11 9"><rect x=".5" y=".5" width="10" height="8" fill="none" stroke="#fff"/><path d="M.5 .5 L5.5 5 L10.5 .5" fill="none" stroke="#fff"/></svg>info@quietmeadownest-example.com</div>
      <div><svg width="10" height="10" viewBox="0 0 10 10"><circle cx="5" cy="5" r="4.4" fill="none" stroke="#fff"/><ellipse cx="5" cy="5" rx="2" ry="4.4" fill="none" stroke="#fff"/><path d="M.6 5H9.4" stroke="#fff"/></svg>www.quietmeadownest-example.com</div>
    </div>
  </section>

  <!-- BACK -->
  <section class="page page--back">
    <div class="photo top-photo" role="img" aria-label="Photo of a baby peeking over white bedding"></div>
    <svg class="wave" style="top:55px" height="95" viewBox="0 0 540 95" aria-hidden="true">
      <path d="M0 20 C140 40 300 60 390 70 C440 50 490 38 540 30 L540 95 L0 95 Z" fill="var(--teal)"/>
      <path d="M0 32 C140 48 300 68 390 80 C440 58 490 44 540 40 L540 95 L0 95 Z" fill="var(--peach)"/>
      <path d="M0 42 C140 56 300 76 390 90 C440 66 490 52 540 48 L540 95 L0 95 Z" fill="#fff"/>
    </svg>

    <div class="abs body-copy intro">
      <p>The Quiet Meadow Nest is a pediatric sleep consultancy that specializes in helping parents with children who struggle to develop good and healthy sleep habits. Disruptive sleep patterns or not enough sleep can affect the physical, mental and emotional development of your child.</p>
      <p>Of course nobody plans to have a sleep problem, but habits can become easily ingrained and spiral quickly out of control and you can find yourself sleep deprived, desperate and not too sure what to do. You see all the other sleeping babies and wish there was someone who understood what you were going through?! Well, there is!</p>
    </div>

    <div class="abs offer-band"></div>
    <h2 class="abs offer-title">Contact me for a free<br>15 minute consultation</h2>
    <p class="abs offer-side">This 15 minute „mini“ consultation is a chance to discuss your unique sleep challenges and sleep goals with me. I will provide you with an overview of how I will work with your family to achieve your wildest sleep dreams (goals).</p>
    <p class="abs offer-more">Furthermore do I understand and believe that every child and their family is unique and there is no one size fits all! I would love to have a chat with you and talk about how I can help make things easier for you and your family!</p>

    <h3 class="abs section-title" style="top:408px">Do I need a sleep consultant for my child?<br>The answer is yes if:</h3>
    <ul class="abs checklist" style="top:448px">
      <li><svg width="10" height="10" viewBox="0 0 10 10"><circle cx="5" cy="5" r="4.4" fill="none" stroke="var(--peach-text)"/><path d="M2.8 5.1 L4.4 6.6 L7.3 3.5" fill="none" stroke="var(--peach-text)"/></svg>If your child will only fall asleep when nursing or bottle feeding</li>
      <li><svg width="10" height="10" viewBox="0 0 10 10"><circle cx="5" cy="5" r="4.4" fill="none" stroke="var(--peach-text)"/><path d="M2.8 5.1 L4.4 6.6 L7.3 3.5" fill="none" stroke="var(--peach-text)"/></svg>If your child needs a dummy or other external aid, like being rocked, patted or taken for a care ride to fall asleep</li>
      <li><svg width="10" height="10" viewBox="0 0 10 10"><circle cx="5" cy="5" r="4.4" fill="none" stroke="var(--peach-text)"/><path d="M2.8 5.1 L4.4 6.6 L7.3 3.5" fill="none" stroke="var(--peach-text)"/></svg>If your good night routine is a challenging and exhausting procedure instead of a relaxed and enjoyable moment for the whole family</li>
      <li><svg width="10" height="10" viewBox="0 0 10 10"><circle cx="5" cy="5" r="4.4" fill="none" stroke="var(--peach-text)"/><path d="M2.8 5.1 L4.4 6.6 L7.3 3.5" fill="none" stroke="var(--peach-text)"/></svg>If sleep is a constant battle in your home which leaves you feeling frustrated and exhausted</li>
      <li><svg width="10" height="10" viewBox="0 0 10 10"><circle cx="5" cy="5" r="4.4" fill="none" stroke="var(--peach-text)"/><path d="M2.8 5.1 L4.4 6.6 L7.3 3.5" fill="none" stroke="var(--peach-text)"/></svg>If your own lack of sleep is taking a toll on you and the whole family</li>
    </ul>

    <h3 class="abs section-title" style="top:553px">What can I do for you?<br>I will:</h3>
    <ul class="abs checklist" style="top:593px">
      <li><svg width="10" height="10" viewBox="0 0 10 10"><circle cx="5" cy="5" r="4.4" fill="none" stroke="var(--peach-text)"/><path d="M2.8 5.1 L4.4 6.6 L7.3 3.5" fill="none" stroke="var(--peach-text)"/></svg>Guide you to set an age appropriate foundation for good sleep</li>
      <li><svg width="10" height="10" viewBox="0 0 10 10"><circle cx="5" cy="5" r="4.4" fill="none" stroke="var(--peach-text)"/><path d="M2.8 5.1 L4.4 6.6 L7.3 3.5" fill="none" stroke="var(--peach-text)"/></svg>Create an individual sleep plan tailored especially to your child’s sleep needs and circumstances</li>
      <li><svg width="10" height="10" viewBox="0 0 10 10"><circle cx="5" cy="5" r="4.4" fill="none" stroke="var(--peach-text)"/><path d="M2.8 5.1 L4.4 6.6 L7.3 3.5" fill="none" stroke="var(--peach-text)"/></svg>Help you to teach your childto go to sleep and get back to sleep independently during the night</li>
      <li><svg width="10" height="10" viewBox="0 0 10 10"><circle cx="5" cy="5" r="4.4" fill="none" stroke="var(--peach-text)"/><path d="M2.8 5.1 L4.4 6.6 L7.3 3.5" fill="none" stroke="var(--peach-text)"/></svg>Show you how to teach your child to take healthful, restorative naps</li>
      <li><svg width="10" height="10" viewBox="0 0 10 10"><circle cx="5" cy="5" r="4.4" fill="none" stroke="var(--peach-text)"/><path d="M2.8 5.1 L4.4 6.6 L7.3 3.5" fill="none" stroke="var(--peach-text)"/></svg>Learn</li>
    </ul>

    <svg class="abs" style="left:0;top:676px" width="540" height="90" viewBox="0 0 540 90" aria-hidden="true">
      <path d="M0 10 C140 -2 280 0 420 8 L540 14 L540 90 L0 90 Z" fill="#f1f1f1"/>
      <path d="M0 8 C140 -4 280 -2 420 6 L540 12" fill="none" stroke="var(--peach)" stroke-width="2"/>
    </svg>
    <div class="photo back-photo" role="img" aria-label="Photo of a baby sleeping with a soft plush toy"></div>

    <div class="abs contact-back">
      <div><svg width="10" height="10" viewBox="0 0 10 10"><circle cx="5" cy="3" r="2.3" fill="var(--peach-text)"/><path d="M1 10 C1 6 9 6 9 10Z" fill="var(--peach-text)"/></svg>MARTA LINDQVIST &nbsp;<svg width="10" height="10" viewBox="0 0 10 10"><path d="M2 1 L4 1 L5 3.5 L3.7 4.5 C4.3 5.8 5 6.5 6.3 7.2 L7.4 6 L9.6 7 L9.4 9 C5 9.5 0.6 5 1.2 1.3Z" fill="#333"/></svg>+34 612 384 705</div>
      <div><svg width="11" height="9" viewBox="0 0 11 9"><rect x=".5" y=".5" width="10" height="8" fill="none" stroke="#333"/><path d="M.5 .5 L5.5 5 L10.5 .5" fill="none" stroke="#333"/></svg>info@quietmeadownest-example.com</div>
      <div><svg width="10" height="10" viewBox="0 0 10 10"><circle cx="5" cy="5" r="4.4" fill="none" stroke="#333"/><ellipse cx="5" cy="5" rx="2" ry="4.4" fill="none" stroke="#333"/><path d="M.6 5H9.4" stroke="#333"/></svg>www.quietmeadownest-example.com</div>
    </div>
  </section>

</main>
</body>
</html>
```